BorrowNest Website design, we are a home loan / lending company

We are a finance broking company that can do mortgages / home loans, Car Loans, Commercial Loans, SMSF Loans, Business Loans, Personal Loans
We are looking for a simple website, not too busy, easy to navigate, something that prompts customers to action or call us.
I like the simplicity of the following websites:
https://www.velkarafinance.com.au/ - I like this website front page. I was thinking I have my logo, the one with the black background appear , then the toolbar at the top perhaps?
https://trevix.com.au/business-loans# - on this page there are images under finance that works for you that I like that concept.
https://dunmerel.com.au/contact/ - I like the Make an Appointment page
https://trevix.com.au/about-us - Simple but effective page design

Target Market(s)

Home Loan Customer

Industry/Entity Type

Finance / Home Loans

Coding

Coded - Design and coding required

Number of Pages Required

5+ page

Font styles to use
Serif

Colors
0094D4
00A9DD
6FCCEA
C7EBF8
E9F6FB

Requirements
Must have
• The following Heading s - Contact Us, About Us, Our People, Make an Appointment, Loan Options, Calculators, Reviews. I want to use the Logo colours I have in the zip files I uploaded.
Nice to have
• Simple clean design

```html
<!DOCTYPE html>
<html lang="en">
<head>
<meta charset="utf-8">
<title>BorrowNest – Home</title>
<link href="https://fonts.googleapis.com/css2?family=Poppins:wght@300;400;500;600;700&family=Lato:wght@400;700&display=swap" rel="stylesheet">
<style>
:root{
  --blue:#00a9e8;
  --blue-deep:#0094d4;
  --navy:#0c1a30;
  --ink:#111;
  --text:#333;
  --muted:#8a8a8a;
  --grey-band:#b3b3b3;
  --light:#f4f4f4;
  --footer:#232323;
  --star:#f5b400;
  --white:#fff;
}
*{box-sizing:border-box;margin:0;padding:0}
html,body{width:1200px;height:3821px;overflow:hidden}
body{position:relative;background:var(--white);font-family:'Lato',sans-serif;color:var(--text)}
.abs{position:absolute}
.heading{font-family:'Poppins',sans-serif}
h2,h3,h4,h5{font-weight:400}
.brand{font-family:'Poppins',sans-serif;font-weight:600;font-size:42px;color:var(--ink);letter-spacing:-1px;line-height:1.2}
.btn{position:absolute;display:flex;align-items:center;justify-content:center;background:var(--blue);color:#fff;font-family:'Poppins',sans-serif;font-weight:600;font-size:15px;border-radius:30px;text-transform:uppercase}

/* header */
.topbar{left:512px;top:0;width:578px;height:37px}
.topbar-items{left:566px;top:0;height:37px;display:flex;gap:32px;align-items:center;color:#fff;font-size:15px}
.topbar-items span{display:flex;align-items:center;gap:8px}
.logo{left:111px;top:18px}
.nav{left:468px;top:60px;display:flex;gap:31px;font-size:15.5px;color:#222}
.nav .active{color:var(--blue);position:relative}
.nav .active:after{content:"";position:absolute;left:2px;right:2px;top:29px;height:3px;background:var(--blue)}

/* hero */
.hero-photo{left:0;top:101px;width:1200px;height:730px}
.hero-title-sm{left:111px;top:268px;font-size:41px;line-height:50px;font-weight:400;color:#1a1a1a}
.hero-title{left:108px;top:318px;font-size:60px;line-height:72px;font-weight:700;color:#111;letter-spacing:.5px}
.hero-text{left:111px;top:402px;width:460px;font-size:15px;line-height:26px;color:#222}

/* about */
.about-photo{position:absolute}
.dot{position:absolute;border-radius:50%}
.eyebrow{left:639px;top:866px;font-size:15px;font-weight:600;color:var(--blue)}
.about-title{left:639px;top:893px;font-size:34px;line-height:46px;color:#111;text-transform:uppercase;font-weight:400}
.about-title b{font-weight:700}
.about-rule{left:603px;top:994px;width:40px;height:2px;background:var(--navy)}
.about-text{left:639px;top:1015px;width:448px;font-size:15px;line-height:26px;color:#333}

/* services */
.services-title{left:0;width:1200px;top:1532px;text-align:center;font-size:35px;color:#fff;font-weight:300}
.services-title b{font-weight:700}
.rule{position:absolute;width:70px;height:2px;background:var(--blue)}
.services-text{left:300px;width:600px;top:1608px;text-align:center;color:#fff;font-size:15px;line-height:26px}
.service{position:absolute;top:1692px;width:307px;height:292px}
.service .img{width:307px;height:230px;border-radius:6px 6px 0 0}
.service .label{position:absolute;left:28px;top:202px;width:245px;height:90px;background:#fff;border-radius:5px;text-align:center;padding-top:22px}
.service h3{font-family:'Poppins',sans-serif;font-weight:600;font-size:20px;color:#111}
.service a{display:inline-block;margin-top:8px;font-family:'Poppins',sans-serif;font-weight:600;font-size:12px;color:var(--blue);border-bottom:2px solid var(--blue);padding-bottom:4px;text-decoration:none}

/* testimonials */
.section-title{left:0;width:1200px;text-align:center;font-size:35px;color:#111;font-weight:400}
.section-title b{font-weight:700}
.review{position:absolute;top:2358px;width:323px;height:323px;padding:30px 0 0 0}
.review.featured{background:#fff;border-radius:18px;box-shadow:0 6px 30px rgba(0,0,0,.08)}
.stars{color:var(--star);font-size:25px;letter-spacing:5px}
.review p{margin-top:14px;width:282px;font-size:15px;line-height:26px;color:var(--muted)}
.person{display:flex;align-items:center;gap:14px;margin-top:14px}
.avatar{width:51px;height:51px;border-radius:50%;background:radial-gradient(circle at 50% 40%,#c9a58a,#5a6c80)}
.person strong{display:block;font-family:'Poppins',sans-serif;font-weight:500;font-size:16px;color:#111}
.person small{font-size:13px;color:var(--muted)}

/* contact */
.contact-bg{left:0;top:2770px;width:1200px;height:470px;background:var(--light)}
.info{position:absolute;left:114px;display:flex;gap:14px}
.info .ico{width:50px;height:50px;border:2px solid var(--blue);border-radius:50%;display:flex;align-items:center;justify-content:center;flex:none}
.info h4{font-family:'Poppins',sans-serif;font-weight:500;font-size:20px;color:#111;text-transform:uppercase}
.info p{font-size:15px;line-height:24px;color:#222;margin-top:2px}
.field{position:absolute;background:#fff;font-size:15px;color:#999;padding:16px 24px}
.submit{position:absolute;left:436px;top:3137px;width:319px;height:53px;background:var(--blue);color:#fff;font-family:'Poppins',sans-serif;font-weight:600;font-size:15px;display:flex;align-items:center;justify-content:center}

/* footer */
.foot-logo{left:111px;top:3455px;color:#fff;font-size:38px}
.foot-about{left:111px;top:3523px;width:240px;font-size:13px;line-height:25px;color:#eee}
.socials{left:111px;top:3620px;display:flex;gap:8px}
.socials span{width:31px;height:31px;border-radius:50%;background:#fff;display:flex;align-items:center;justify-content:center}
.socials span i{width:9px;height:9px;border-radius:50%;background:var(--blue-deep)}
.foot-col{position:absolute;top:3466px}
.foot-col h5{font-family:'Poppins',sans-serif;font-weight:600;font-size:17px;color:#fff;text-transform:uppercase}
.foot-col h5:after{content:"";display:block;width:36px;height:2px;background:var(--blue);margin-top:10px}
.foot-col ul{list-style:none;margin-top:14px}
.foot-col li{font-size:15px;line-height:30px;color:#fff;padding-left:3px}
.foot-col p{font-size:15px;line-height:26px;color:#eee;margin-top:14px;width:290px}
.newsletter{left:801px;top:3580px;width:275px;height:44px;background:#fff;border-radius:24px;font-size:14px;color:#999;padding:13px 20px}
.send{left:1031px;top:3580px;width:45px;height:45px;border-radius:50%;background:var(--blue);display:flex;align-items:center;justify-content:center}
.copyright{left:0;width:1200px;top:3760px;text-align:center;color:#fff;font-size:15px}
.copyright span{color:var(--blue);text-decoration:underline}
</style>
</head>
<body>

<!-- Header -->
<svg class="abs topbar" viewBox="0 0 578 37" width="578" height="37"><polygon points="0,0 578,0 555,37 36,37" fill="var(--blue)"/></svg>
<div class="abs topbar-items">
  <span><svg width="15" height="15" viewBox="0 0 24 24"><path d="M6.6 10.8a15 15 0 0 0 6.6 6.6l2.2-2.2c.3-.3.7-.4 1-.2 1.1.4 2.3.6 3.6.6.6 0 1 .4 1 1V20c0 .6-.4 1-1 1A17 17 0 0 1 3 4c0-.6.4-1 1-1h3.5c.6 0 1 .4 1 1 0 1.3.2 2.5.6 3.6.1.3 0 .7-.2 1z" fill="#fff"/></svg>+1 555 014 2290</span>
  <span><svg width="15" height="12" viewBox="0 0 24 18"><rect width="24" height="18" rx="2" fill="#fff"/><path d="M1 2l11 8 11-8" stroke="var(--blue)" stroke-width="2" fill="none"/></svg>info@borrownest.com</span>
  <span><svg width="14" height="14" viewBox="0 0 24 24"><path d="M10 4h10v16H10v-2h8V6h-8zM2 11h10V7l6 5-6 5v-4H2z" fill="#fff"/></svg>Login</span>
</div>
<div class="abs logo brand">BorrowNest</div>
<nav class="abs nav">
  <span class="active">Home</span><span>About Us</span><span>Our People</span><span>Make an Appointment</span><span>Contact Us</span><span>More</span>
</nav>

<!-- Hero -->
<svg class="abs hero-photo" viewBox="0 0 1200 730" width="1200" height="730" role="img" aria-label="Photo of a woman working on a laptop at a bright office desk">
  <defs><linearGradient id="heroG" x1="0" x2="1" y1="0" y2="0"><stop offset="0" stop-color="#ececec"/><stop offset=".55" stop-color="#e2e2e0"/><stop offset=".75" stop-color="#bfb7ae"/><stop offset="1" stop-color="#d4d6d8"/></linearGradient></defs>
  <polygon points="0,0 1200,0 1200,534 0,679" fill="url(#heroG)"/>
  <polygon points="308,660 1200,532 1200,553 308,680" fill="var(--grey-band)"/>
  <polygon points="808,603 1200,537 1200,729" fill="var(--blue)"/>
</svg>
<div class="abs heading hero-title-sm">WELCOME TO</div>
<div class="abs heading hero-title">BORROWNEST</div>
<p class="abs hero-text">Lorem ipsum dolor sit amet, consectetur adipiscing elit, sed do eiusmod tempor incididunt ut labore et dolore</p>
<div class="btn" style="left:111px;top:470px;width:163px;height:53px">Get Started</div>

<!-- About -->
<div class="dot" style="left:387px;top:851px;width:30px;height:30px;background:var(--blue)"></div>
<div class="dot" style="left:570px;top:1018px;width:29px;height:29px;background:#d0d0d0"></div>
<div class="dot" style="left:163px;top:1209px;width:31px;height:31px;background:var(--navy)"></div>
<div class="about-photo" style="left:153px;top:882px;width:218px;height:223px;background:linear-gradient(135deg,#8a7668,#2a3446 60%,#cfd3d8)" role="img" aria-label="Photo of colleagues meeting around a table"></div>
<div class="about-photo" style="left:378px;top:963px;width:144px;height:142px;background:linear-gradient(135deg,#a08a6a,#e8e4dc)" role="img" aria-label="Photo of a woman working at a desk"></div>
<div class="about-photo" style="left:266px;top:1112px;width:107px;height:107px;background:linear-gradient(135deg,#6d8a7a,#c0793e 55%,#d9d9d9)" role="img" aria-label="Photo of a small model house"></div>
<div class="about-photo" style="left:378px;top:1112px;width:170px;height:171px;background:linear-gradient(135deg,#c9ccd0,#6f625a 60%,#b5a89a)" role="img" aria-label="Photo of a handshake over a model house"></div>
<div class="abs eyebrow heading">ABOUT US</div>
<h2 class="abs heading about-title"><b>Lorem ipsum dolor sit</b><br>amet, consectetur</h2>
<div class="abs about-rule"></div>
<p class="abs about-text">Lorem ipsum dolor sit amet, consectetur adipiscing elit, sed do eiusmod tempor incididunt ut labore et dolore magna aliqua. Quis ipsum suspendisse ultrices gravida. Risus commodo viverra maecenas accumsan lacus vel facilisis. Lorem ipsum dolor sit amet, consectetur adipiscing elit, sed do eiusmod tempor incididunt ut labore et dolore magna aliqua. Quis ipsum suspendisse ultrices gravida. Risus commodo viverra maecenas accumsan lacus vel facilisis. Lorem ipsum dolor sit amet,</p>
<div class="btn" style="left:636px;top:1238px;width:165px;height:55px">Learn More</div>

<!-- Services -->
<svg class="abs" style="left:0;top:1340px" width="1200" height="912" viewBox="0 0 1200 912" role="img" aria-label="Dark blue background photo of a business meeting">
  <defs><linearGradient id="svcG" x1="0" x2="1"><stop offset="0" stop-color="#0d1c33"/><stop offset=".7" stop-color="#132742"/><stop offset="1" stop-color="#1b2d45"/></linearGradient></defs>
  <polygon points="0,200 1200,53 1200,705 0,910" fill="url(#svcG)"/>
  <polygon points="0,180 890,72 890,92 0,200" fill="var(--grey-band)"/>
  <polygon points="0,2 385,132 0,180" fill="var(--blue)"/>
</svg>
<h2 class="abs heading services-title">OUR <b>SERVICES</b></h2>
<div class="rule" style="left:565px;top:1586px"></div>
<p class="abs services-text">Lorem ipsum dolor sit amet, consectetur adipiscing elit, sed do eiusmod tempor incididunt ut labore et dolore magna aliqua.</p>
<div class="service" style="left:111px">
  <div class="img" style="background:linear-gradient(135deg,#5b4b3e,#d7d2cb 60%,#8f8a84)" role="img" aria-label="Photo of a loan agreement being signed"></div>
  <div class="label"><h3>HOME LOANS</h3><a>LEARN MORE</a></div>
</div>
<div class="service" style="left:446px">
  <div class="img" style="background:linear-gradient(135deg,#8a7668,#2a3446 60%,#cfd3d8)" role="img" aria-label="Photo of a car loan consultation"></div>
  <div class="label"><h3>CAR LOANS</h3><a>LEARN MORE</a></div>
</div>
<div class="service" style="left:782px">
  <div class="img" style="background:linear-gradient(135deg,#3a3a3e,#b9b2a6 60%,#e6e2dc)" role="img" aria-label="Photo of a commercial loan review"></div>
  <div class="label"><h3>COMMERCIAL LOANS</h3><a>LEARN MORE</a></div>
</div>
<div class="btn" style="left:521px;top:2044px;width:157px;height:53px">View More</div>

<!-- Testimonials -->
<h2 class="abs heading section-title" style="top:2260px">WHAT PEOPLE <b>ARE SAYING</b></h2>
<div class="rule" style="left:565px;top:2319px"></div>
<div class="review" style="left:123px">
  <div class="stars">★★★★★</div>
  <p>Lorem ipsum dolor sit amet, consectetur adipiscing elit, sed do eiusmod tempor incididunt ut labore et dolore magna aliqua. Quis ipsum suspendisse ultrices gravida. Risus commodo viverra maecenas accumsan lacus vel facilisis.</p>
  <div class="person"><div class="avatar" role="img" aria-label="Client portrait"></div><div><strong>Marlow Pennick</strong><small>Lorem Ipsum</small></div></div>
</div>
<div class="review featured" style="left:430px;padding-left:31px">
  <div class="stars">★★★★★</div>
  <p>Lorem ipsum dolor sit amet, consectetur adipiscing elit, sed do eiusmod tempor incididunt ut labore et dolore magna aliqua. Quis ipsum suspendisse ultrices gravida. Risus commodo viverra maecenas accumsan lacus vel facilisis.</p>
  <div class="person"><div class="avatar" role="img" aria-label="Client portrait"></div><div><strong>Marlow Pennick</strong><small>Lorem Ipsum</small></div></div>
</div>
<div class="review" style="left:799px">
  <div class="stars">★★★★★</div>
  <p>Lorem ipsum dolor sit amet, consectetur adipiscing elit, sed do eiusmod tempor incididunt ut labore et dolore magna aliqua. Quis ipsum suspendisse ultrices gravida. Risus commodo viverra maecenas accumsan lacus vel facilisis.</p>
  <div class="person"><div class="avatar" role="img" aria-label="Client portrait"></div><div><strong>Marlow Pennick</strong><small>Lorem Ipsum</small></div></div>
</div>

<!-- Contact -->
<div class="abs contact-bg"></div>
<h2 class="abs heading section-title" style="top:2826px">CONTACT <b>US</b></h2>
<div class="rule" style="left:565px;top:2883px"></div>
<div class="info" style="top:2932px">
  <div class="ico"><svg width="16" height="20" viewBox="0 0 16 20"><path d="M8 0a8 8 0 0 1 8 8c0 6-8 12-8 12S0 14 0 8a8 8 0 0 1 8-8z" fill="var(--blue)"/><circle cx="8" cy="8" r="3" fill="#fff"/></svg></div>
  <div><h4>Location</h4><p>Lorem ipsum dolor sit amet, con-<br>sectetur adipiscing elit</p></div>
</div>
<div class="info" style="top:3037px">
  <div class="ico"><svg width="17" height="17" viewBox="0 0 24 24"><path d="M6.6 10.8a15 15 0 0 0 6.6 6.6l2.2-2.2c.3-.3.7-.4 1-.2 1.1.4 2.3.6 3.6.6.6 0 1 .4 1 1V20c0 .6-.4 1-1 1A17 17 0 0 1 3 4c0-.6.4-1 1-1h3.5c.6 0 1 .4 1 1 0 1.3.2 2.5.6 3.6.1.3 0 .7-.2 1z" fill="var(--blue)"/></svg></div>
  <div><h4>Phone</h4><p>+1 555 014 2290</p></div>
</div>
<div class="info" style="top:3133px">
  <div class="ico"><svg width="16" height="12" viewBox="0 0 24 18"><rect width="24" height="18" rx="2" fill="var(--blue)"/><path d="M1 2l11 8 11-8" stroke="#fff" stroke-width="2" fill="none"/></svg></div>
  <div><h4>Email</h4><p>info@borrownest.com</p></div>
</div>
<div class="field" style="left:436px;top:2932px;width:319px;height:52px">Name</div>
<div class="field" style="left:436px;top:2999px;width:319px;height:53px">Phone</div>
<div class="field" style="left:436px;top:3067px;width:319px;height:53px">Email</div>
<div class="submit">SUBMIT</div>
<div class="field" style="left:774px;top:2932px;width:301px;height:258px">Type your message</div>

<!-- Footer -->
<svg class="abs" style="left:0;top:3230px" width="1200" height="591" viewBox="0 0 1200 591">
  <polygon points="0,190 1200,40 1200,591 0,591" fill="var(--footer)"/>
  <polygon points="0,172 890,70 890,90 0,192" fill="var(--grey-band)"/>
  <polygon points="0,0 385,127 0,172" fill="var(--blue)"/>
</svg>
<div class="abs brand foot-logo">BorrowNest</div>
<p class="abs foot-about">Lorem ipsum dolor sit amet, consectetur adipiscing elit, sed do eiusmod tempor incididunt ut labore et</p>
<div class="abs socials"><span><i></i></span><span><i></i></span><span><i></i></span><span><i></i></span></div>
<div class="foot-col" style="left:417px"><h5>Quick Link</h5><ul><li>Home</li><li>About Us</li><li>Our People</li><li>Make an Appointment</li><li>Contact Us</li><li>More</li></ul></div>
<div class="foot-col" style="left:624px"><h5>Support</h5><ul><li>Terms &amp; Conditions</li><li>Privacy Policy</li><li>About Us</li><li>Support</li></ul></div>
<div class="foot-col" style="left:801px"><h5>Subscribe to our newsletter</h5><p>Lorem ipsum dolor sit amet, consectetur adipiscing elit, sed do</p></div>
<div class="abs newsletter">Enter Your Email</div>
<div class="abs send"><svg width="18" height="18" viewBox="0 0 24 24"><path d="M22 2L2 10l7 3 3 7z" fill="#fff"/></svg></div>
<p class="abs copyright">©Copyrights 2022 <span>BorrowNest</span> &nbsp;| &nbsp; All Rights Reserved</p>

</body>
</html>
```